High Tech Real Estate Startup needs a business card

We are developing an innovative real estate marketing product based around advanced search and virtual reality.

We talk to people, we need business cards.

Target Market(s)

The target market is technology professionals and realtors.

Contact Information for Business Card

The information to be included will include

Name
Title
Phone Number
E-mail Address
www.zelquin.com

It should use simple iconography for each one of those fields.

Font styles to use
Other font styles liked:
• Co, Jubilat, Avenir

Colors

Designer to choose colors to be used in the design.

Requirements
Must have
• Clean aesthetic,
• Good use of negative space.
• It should use our company logo, shown in the attached file. It is able to use the negative of that logo (coloured font and white background) and I have attached other acceptable accent colours in a swatch file.
Should not have
• Should not be too busy
• No extraneous text (slogans, tag lines etc)

```html
<!DOCTYPE html>
<html lang="en">
<head>
<meta charset="utf-8">
<title>Zelquin business card</title>
<link rel="stylesheet" href="https://fonts.googleapis.com/css2?family=Open+Sans:wght@400;600;700&display=swap">
<style>
  :root {
    --teal: #00b8bd;
    --paper: #ffffff;
    --ink-grey: #6f7173;
    --ink-dark: #55585a;
    --backdrop: #ece9e4;
  }
  * { margin: 0; padding: 0; box-sizing: border-box; }
  html, body {
    width: 1200px; height: 911px; overflow: hidden;
    background: var(--backdrop);
    font-family: "Open Sans", Arial, sans-serif;
  }
  .card-stage {
    width: 1200px; height: 911px;
    display: flex; flex-direction: column;
    align-items: center; justify-content: center;
    gap: 56px;
  }
  .card {
    width: 620px; height: 354px;
    position: relative; overflow: hidden;
    box-shadow: 0 6px 18px rgba(0,0,0,0.18);
  }
  /* front */
  .card-front { background: var(--paper); display: flex; }
  .front-brand {
    width: 340px; height: 100%;
    background: var(--teal);
    display: flex; align-items: center; justify-content: center;
  }
  .front-divider {
    width: 8px; height: 100%;
    margin-left: 10px;
    background: var(--teal);
  }
  .front-details {
    flex: 1;
    display: flex; flex-direction: column; justify-content: center;
    padding-left: 30px;
    white-space: nowrap;
  }
  .brand-name {
    color: var(--paper);
    font-weight: 600;
    letter-spacing: 0.04em;
    line-height: 1;
    white-space: nowrap;
  }
  .front-brand .brand-name { font-size: 52px; }
  .person-name {
    color: var(--teal); font-weight: 700; font-size: 19px;
    letter-spacing: 0.02em; line-height: 1.2;
  }
  .person-title {
    color: var(--ink-dark); font-weight: 700; font-size: 14px;
    margin-bottom: 10px;
  }
  .contact-line {
    color: var(--ink-grey); font-size: 12.5px; line-height: 1.6;
  }
  .contact-web { letter-spacing: 0.28em; }
  /* back */
  .card-back {
    background: var(--teal);
    display: flex; align-items: center; justify-content: center;
  }
  .back-lockup { display: flex; flex-direction: column; align-items: flex-start; }
  .card-back .brand-name { font-size: 68px; }
  .back-web {
    color: var(--paper); font-size: 12px;
    letter-spacing: 0.35em; margin-top: 22px; margin-left: 6px;
    white-space: nowrap;
  }
</style>
</head>
<body>
<main class="card-stage">
  <section class="card card-front">
    <div class="front-brand"><span class="brand-name">ZELQUIN</span></div>
    <div class="front-divider"></div>
    <div class="front-details">
      <p class="person-name">ADAM REYES</p>
      <p class="person-title">CEO/Founder</p>
      <p class="contact-line">555 019 7346 | adam@zelquin.com</p>
      <p class="contact-line contact-web">www.zelquin.com</p>
    </div>
  </section>
  <section class="card card-back">
    <div class="back-lockup">
      <span class="brand-name">ZELQUIN</span>
      <span class="back-web">WWW.ZELQUIN.COM</span>
    </div>
  </section>
</main>
</body>
</html>
```